Bram Keystone Homes needs a business card

We need a business card for a new company in Canada, Ontario. Our company is all about luxury contraction homes for our clients. Our product and services are custom projects design. Under the business logo that will be created, we want a slogan that will be a memorable phrase for consumers to remember us to tell their friends and relatives.

Additional infomation
- Ludovic Entrasse
- President / Ceo
-519.604.3087

Find point what luxury construction products and services can be done

We like to see colors:
- #663300
- and something other colors or color that would attract the client needs and wants

The final design should communicate leads from new or old clients that will grow our empire. Most of all, we try to work among the budget that clients want

NOTE
- we also need an icon for the business (Example: Instagram, Facebook, and Whatsapp icons)
- We want the company name to be remembered easily for clients and our distributors who would get our orders.
- we need an icon on the business cards: Facebook and Instagram.

Thanks,
Bram Keystone Homes

```html
<!DOCTYPE html>
<html lang="en">
<head>
<meta charset="UTF-8">
<title>Bram Keystone Homes — Business Card</title>
<link rel="stylesheet" href="https://fonts.googleapis.com/css2?family=Roboto+Condensed:wght@500;700&family=Poppins:wght@400;500&display=swap">
<style>
  :root {
    --brand-brown: #663300;
    --ink-grey: #4a4a4a;
    --card-white: #ffffff;
    --backdrop: #2b2b2b;
  }
  * { margin: 0; padding: 0; box-sizing: border-box; }
  html, body {
    width: 1200px;
    height: 874px;
    overflow: hidden;
    background: var(--backdrop);
  }
  .sheet {
    width: 1200px;
    height: 874px;
    display: flex;
    flex-direction: column;
    align-items: center;
    justify-content: center;
    gap: 34px;
  }
  .card {
    width: 620px;
    height: 354px;
    background: var(--card-white);
    position: relative;
    display: flex;
    flex-direction: column;
    align-items: center;
    color: var(--brand-brown);
  }
  .wordmark {
    font-family: "Roboto Condensed", sans-serif;
    font-weight: 700;
    color: var(--brand-brown);
    text-align: center;
    line-height: 1;
  }
  .wordmark__name {
    font-size: 46px;
    letter-spacing: 0.5px;
  }
  .wordmark__tagline {
    font-size: 17px;
    letter-spacing: 0.4px;
    margin-top: 6px;
  }
  .card--front { padding-top: 118px; }
  .social-row {
    position: absolute;
    bottom: 44px;
    left: 50%;
    transform: translateX(-50%);
    display: flex;
    gap: 5px;
  }
  .social-row svg { display: block; }
  .card--back { padding-top: 92px; }
  .card--back .wordmark__name { font-size: 38px; }
  .card--back .wordmark__tagline { font-size: 15px; }
  .contact {
    margin-top: 42px;
    text-align: center;
    font-family: "Poppins", sans-serif;
  }
  .contact__name {
    font-size: 27px;
    font-weight: 500;
    color: var(--brand-brown);
    letter-spacing: 0.5px;
  }
  .contact__role {
    font-size: 19px;
    color: var(--ink-grey);
    margin-top: 2px;
  }
  .contact__phone {
    font-size: 17px;
    color: var(--ink-grey);
    letter-spacing: 0.5px;
    margin-top: 2px;
  }
</style>
</head>
<body>
<main class="sheet">
  <section class="card card--front">
    <div class="wordmark">
      <div class="wordmark__name">Bram Keystone Homes</div>
      <div class="wordmark__tagline">- HOME RENOVATIONS - CUSTOM PROJECT DESIGN -</div>
    </div>
    <div class="social-row" aria-label="Social media links">
      <svg width="30" height="30" viewBox="0 0 30 30" role="img" aria-label="Social profile"><circle cx="15" cy="15" r="13.5" fill="none" stroke="var(--brand-brown)" stroke-width="1.2"/></svg>
      <svg width="30" height="30" viewBox="0 0 30 30" role="img" aria-label="Social profile"><circle cx="15" cy="15" r="13.5" fill="none" stroke="var(--brand-brown)" stroke-width="1.2"/></svg>
      <svg width="30" height="30" viewBox="0 0 30 30" role="img" aria-label="Messaging contact"><circle cx="15" cy="15" r="13.5" fill="none" stroke="var(--brand-brown)" stroke-width="1.2"/></svg>
    </div>
  </section>

  <section class="card card--back">
    <div class="wordmark">
      <div class="wordmark__name">Bram Keystone Homes</div>
      <div class="wordmark__tagline">- HOME RENOVATIONS - CUSTOM PROJECT DESIGN -</div>
    </div>
    <div class="contact">
      <div class="contact__name">Ludovic Entrasse</div>
      <div class="contact__role">President / Ceo</div>
      <div class="contact__phone">519.604.3087</div>
    </div>
  </section>
</main>
</body>
</html>
```